Business Intelligence Application - Reporting Menu and Report Criteria Design

Looking for a fresh, effective and user friendly view for the menu structure and reporting criteria screen format for a business reporting application. Initial format completed, content structure is in place, but we need the 'wow' design.. as its a serious professional report/BI tool it has to fall within certain guidelines for clarity and graphics..but we want it to be slick, friendly, great user experience. There is a large amount of complex content to fit into a small space and we need it to be very inviting, modern and intuitive.. If interested, please review the attachment. We have live screens in operation, but feel these could be improved and looking forward to seeing what great creative suggestions could be made. Please review work done to date in the attached.. We are not looking for a total re-design of everything, all the basic business content/structure is there.. but tell us what we could do to improve this in terms of graphic design... particularly the criteria screens.. thanks!
Updates

Reason: Need a few more days to review designs - thanks for all submissions so far, we will make a selection shortly.

Target Market(s)

Business analysts, hotel operations teams, finance analysts hospitality industry

Industry/Entity Type

Hospitality

Coding

Coded - Design and coding required

Number of Pages Required

4 page

Font styles to use
Sans Serif
Other font styles liked:
• Candara, please see example in deck

Colors
3276b5
3176b5
0255a3
85acd3
33a6d7
cee9f5
85cae6

Requirements
Must have
• sharp clear, logical menu structure, (currently it has 'clicks to sub-menus, we need hover over, slide to sub-menus..) colour, styling.. and most focus on revision of criteria.. right now is somewhat heavy, cumbersome.. keep colour and friendly intuitive process steps.. its heavy analytical stuff.. best of luck!
Should not have
• No grey fonts on white or grey screens! many business apps are not readable or sharp.. or fonts are too small.. colourless, so please avoid that.. see our deck - sharp dark (navy) or black fonts on white, or light shading..

```html
<!DOCTYPE html>
<html lang="en">
<head>
<meta charset="utf-8">
<title>Silver Tide Hotel &amp; Suites – Admin Menu</title>
<link href="https://fonts.googleapis.com/css2?family=Cabin:wght@400;500;600&display=swap" rel="stylesheet">
<style>
  :root {
    --header-bg: #d2e9f5;
    --brand-blue: #33a6d7;
    --menu-blue: #33a6d7;
    --menu-active: #85cae6;
    --menu-divider: #5fb9e0;
    --ink: #111111;
    --white: #ffffff;
    --border: #8a8a8a;
  }
  * { box-sizing: border-box; margin: 0; padding: 0; }
  html, body { width: 1200px; height: 522px; overflow: hidden; background: var(--white); }
  body { font-family: "Cabin", "Candara", sans-serif; color: var(--ink); position: relative; }

  .app-header {
    position: absolute; left: 0; top: 0; width: 1200px; height: 58px;
    background: var(--header-bg);
  }
  .brand {
    position: absolute; left: 47px; top: 0; height: 58px;
    display: flex; align-items: center; gap: 10px;
    color: var(--brand-blue); font-size: 19px; font-weight: 500;
  }
  .brand-mark { width: 24px; height: 24px; border-radius: 50%; background: var(--brand-blue); }
  .welcome, .today {
    position: absolute; top: 0; line-height: 58px; font-size: 13px; font-weight: 500;
  }
  .welcome { left: 554px; }
  .today { left: 667px; }
  .header-button {
    position: absolute; top: 11px; height: 37px; width: 107px;
    background: var(--brand-blue); color: var(--white);
    font-size: 12.5px; font-weight: 600; letter-spacing: .3px;
    display: flex; align-items: center; justify-content: center;
  }
  .button-intel { left: 832px; }
  .button-planning { left: 954px; }
  .header-icon { position: absolute; top: 16px; }
  .icon-alerts { left: 1083px; }
  .icon-logout { left: 1125px; }

  .main-nav {
    position: absolute; left: 47px; top: 86px; height: 22px;
    display: flex; align-items: center; font-size: 13.5px; font-weight: 500;
  }
  .main-nav .nav-item.is-active { color: var(--brand-blue); }
  .main-nav .nav-dot {
    width: 3px; height: 3px; border-radius: 50%; background: var(--brand-blue);
    margin: 0 8px;
  }
  .property-search {
    position: absolute; left: 775px; top: 79px; width: 376px; height: 38px;
    border: 1px solid var(--border); display: flex; align-items: center;
    padding: 0 14px 0 16px; justify-content: space-between;
    font-size: 11.5px; letter-spacing: .2px;
  }

  .dropdown {
    position: absolute; list-style: none; background: var(--menu-blue);
    box-shadow: 0 2px 6px rgba(0,0,0,.12);
  }
  .dropdown li {
    height: 33.6px; display: flex; align-items: center; justify-content: space-between;
    padding: 0 11px; color: var(--white); font-size: 11.5px;
    border-bottom: 1px solid var(--menu-divider);
  }
  .dropdown li:last-child { border-bottom: none; }
  .dropdown li.is-open { background: var(--menu-active); }
  .admin-menu { left: 49px; top: 124px; width: 163px; }
  .admin-menu::before {
    content: ""; position: absolute; left: 12px; top: -8px;
    border-left: 8px solid transparent; border-right: 8px solid transparent;
    border-bottom: 8px solid var(--menu-blue);
  }
  .setup-menu { left: 211px; top: 196px; width: 164px; }
</style>
</head>
<body>
  <header class="app-header">
    <div class="brand"><span class="brand-mark"></span><span>Silver Tide Hotel &amp; Suites</span></div>
    <div class="welcome">Welcome Admin</div>
    <div class="today">Tuesday October 04.2017</div>
    <div class="header-button button-intel">INTEL</div>
    <div class="header-button button-planning">PLANNING</div>
    <svg class="header-icon icon-alerts" width="28" height="26" viewBox="0 0 28 26" fill="none" stroke="#111" stroke-width="1.3" stroke-linecap="round">
      <path d="M8 18 V11 a6 6 0 0 1 12 0 V18 l2 2 H6 z"/>
      <path d="M12 22 a2 2 0 0 0 4 0"/>
      <path d="M14 3 v2"/>
      <path d="M4 9 q-2 3 0 6 M24 9 q2 3 0 6"/>
    </svg>
    <svg class="header-icon icon-logout" width="30" height="24" viewBox="0 0 30 24" fill="none" stroke="#111" stroke-width="1.4" stroke-linejoin="round">
      <path d="M20 6 H10 a7 7 0 0 0 -7 7 v3"/>
      <path d="M20 2 l7 6 -7 6 v-3 H12 a5 5 0 0 0 -5 5"/>
      <path d="M3 12 v10 h20 v-6"/>
    </svg>
  </header>

  <nav class="main-nav">
    <span class="nav-item is-active">Admin</span><span class="nav-dot"></span>
    <span class="nav-item">Management</span><span class="nav-dot"></span>
    <span class="nav-item">Rooms Performance</span><span class="nav-dot"></span>
    <span class="nav-item">Revenue Summary</span><span class="nav-dot"></span>
    <span class="nav-item">Demand &amp; Risk</span><span class="nav-dot"></span>
    <span class="nav-item">Inventory Analysis</span><span class="nav-dot"></span>
    <span class="nav-item">Placeholder</span>
  </nav>

  <div class="property-search">
    <span>PROPERTY SEARCH</span>
    <svg width="14" height="14" viewBox="0 0 14 14" fill="none" stroke="#111" stroke-width="1.2"><circle cx="6" cy="6" r="4.8"/><path d="M9.5 9.5 L13 13"/></svg>
  </div>

  <ul class="dropdown admin-menu">
    <li>Registration</li>
    <li>User Access</li>
    <li class="is-open">Setup <svg width="6" height="9" viewBox="0 0 6 9"><path d="M0 0 L6 4.5 L0 9z" fill="#fff"/></svg></li>
    <li>Data Imoorts</li>
  </ul>

  <ul class="dropdown setup-menu">
    <li>Market Segments</li>
    <li>Banquet &amp; Catering</li>
    <li>Outlets / F&amp;B Service</li>
    <li>Other Income</li>
    <li>Impact Dates</li>
    <li>Inventory</li>
    <li>Geo/Location</li>
    <li>Distribution Channels</li>
  </ul>
</body>
</html>
```